Bright Wave Labs

We need a professional letter head format for our company. Now we have a logo but need to desing a new logo also. I have uploaded our old logo. Use the color in the logo and design a new one.

Dear Designers , Need to mention "BWL" and please dont use our old LOGO. we need a new catchy one.

```html
<!DOCTYPE html>
<html lang="en">
<head>
<meta charset="utf-8">
<title>Bright Wave Labs – Letterhead</title>
<link href="https://fonts.googleapis.com/css2?family=Open+Sans:wght@400;600;700&family=Lato:wght@400;700&display=swap" rel="stylesheet">
<style>
  :root {
    --navy: #112d4b;
    --green: #9bc43a;
    --body-text: #555a5e;
    --ink: #1c1c1c;
    --rule: #a9bfd0;
    --backdrop: #e8e8e8;
    --paper: #ffffff;
  }
  html, body {
    margin: 0;
    padding: 0;
    width: 1040px;
    height: 1200px;
    overflow: hidden;
    background: var(--backdrop);
  }
  .letterhead {
    position: absolute;
    left: 70px;
    top: 20px;
    width: 900px;
    height: 1160px;
    background: var(--paper);
    font-family: "Open Sans", Arial, sans-serif;
    color: var(--body-text);
  }
  .top-band {
    position: absolute;
    left: 0; top: 0;
    width: 100%;
    height: 23px;
    background: var(--navy);
  }
  .brand {
    position: absolute;
    top: 46px;
    left: 0;
    width: 100%;
    text-align: center;
    font-family: "Open Sans", Arial, sans-serif;
    font-weight: 700;
    font-size: 40px;
    letter-spacing: 1px;
    color: var(--navy);
    line-height: 50px;
  }
  .brand-mark {
    display: inline-block;
    width: 16px;
    height: 16px;
    background: var(--green);
    margin-right: 14px;
    vertical-align: 4px;
  }
  .letter-body {
    position: absolute;
    left: 84px;
    width: 728px;
    font-size: 14.5px;
  }
  .issue-date { top: 240px; }
  .recipient { top: 274px; line-height: 17px; }
  .salutation { top: 372px; }
  .paragraph {
    line-height: 26px;
    text-align: justify;
    hyphens: auto;
    margin: 0;
  }
  .p1 { top: 420px; }
  .p2 { top: 576px; }
  .p3 { top: 681px; }
  .closing { top: 814px; }
  .signatory-name {
    top: 889px;
    font-size: 18px;
    font-weight: 600;
    color: #3a3d40;
  }
  .signatory-title { top: 918px; }
  .footer {
    position: absolute;
    left: 0;
    width: 100%;
    text-align: center;
    font-family: "Lato", Arial, sans-serif;
    font-size: 17px;
    color: var(--ink);
  }
  .footer-address { top: 1060px; }
  .footer-rule {
    position: absolute;
    top: 1089px;
    left: 153px;
    width: 593px;
    height: 1px;
    background: var(--rule);
  }
  .footer-contacts { top: 1095px; }
  .footer-contacts .sep { margin: 0 22px; }
  .footer-contacts .accent { color: var(--green); }
  .bottom-band {
    position: absolute;
    left: 0;
    top: 1134px;
    width: 900px;
    height: 26px;
  }
</style>
</head>
<body>
  <div class="letterhead">
    <div class="top-band"></div>

    <div class="brand"><span class="brand-mark"></span>BRIGHT WAVE LABS</div>

    <div class="letter-body issue-date">Issuing Date: May 5, 2018</div>
    <div class="letter-body recipient">
      Name Of Employee Mr. XYZABC<br>
      Address of Employee<br>
      Address Line 2 etc..
    </div>
    <div class="letter-body salutation">Dear Mr.XYZABC</div>

    <p class="letter-body paragraph p1">Lorem Ipsum has been the industry's standard dummy text ever since the 1500s, when an unknown printer took a galley of type and scrambled it to make a type specimen book. It has survived not only five centuries, but also the leap into electronic typesetting, remaining essentially unchanged. It was popularised in the 1960s with the release of Letraset sheets containing Lorem Ipsum passages, and more recently with desktop publishing software like Aldus PageMaker including versions of Lorem Ipsum.</p>

    <p class="letter-body paragraph p2">Lorem Ipsum is simply dummy text of the printing and typesetting industry. Lorem Ipsum has been the industry's standard dummy text ever since the 1500s, when an unknown printer took a galley of type and scrambled it to make a type specimen book.</p>

    <p class="letter-body paragraph p3">It has survived not only five centuries, but also the leap into electronic typesetting, remaining essentially unchanged. It was popularised in the 1960s with the release of Letraset sheets containing Lorem IpsumIpsum passages.</p>

    <div class="letter-body closing">Yours Sincerely</div>
    <div class="letter-body signatory-name">Marcus Reed</div>
    <div class="letter-body signatory-title">Managing Director</div>

    <div class="footer footer-address">421, Address line here, 45452,Country Name</div>
    <div class="footer-rule"></div>
    <div class="footer footer-contacts">
      P: 044-123 456 789<span class="sep">|</span>E: info@webname.com<span class="sep">|</span>www.<span class="accent">websitename</span>.com
    </div>

    <svg class="bottom-band" viewBox="0 0 900 26" width="900" height="26" aria-hidden="true">
      <rect x="0" y="0" width="900" height="26" fill="var(--green)"/>
      <polygon points="437,0 463,0 450,24" fill="var(--paper)"/>
    </svg>
  </div>
</body>
</html>
```